IV Nutritional Clinic Web Design

We are working with Velqo. They are an IV Nutritional Clinic and in need of a new website design.
Some sites to use for inspiration:
https://brightpathcareco.com
https://www.ourzavrowellness.com
https://www.dewspringlounge.com
https://qvitalsurge.com
https://www.lumo-vital.com/pages/iv-therapy-west-hollywood
https://www.tqoncologyhub.com/cancer-care/iv-drips/
https://dripwellary.com
https://corvinahealthhub.com
Thank you for taking the time to consider designing a website for us. We are web developers based in Stockton, CA, USA. Most of our projects go through the same process. Understanding this process may help you win a project with us. We custom-code all of our websites in-house. We don’t have any requirements as to what tools you use for your design, but we prefer Figma files. For any design that we label as four-stars, we send it to the client for review. The client picks the final design they want us to use. Once we complete this process, we will continue to show additional clients all the four-star sites and purchase them later. Your designs will have multiple chances to sell. For better chances of success, we ask that you follow these guidelines.
IMAGES:
If you use any images or icons in the design, we ask that you have a link to the asset so we can purchase the image/icon. Most of the designs we submit do not have the customer’s images on them unless they have some great images. Be creative; show us the feeling you are trying to portray with your image choices. Use any royalty-free site you choose. We subscribe to Pixvane and mainly use their images, but we can purchase images outside of Pixvane.
PLEASE NOTE: we will not submit designs to clients with watermarks on the images.
FONTS:
We ask that you identify the fonts used in the design. This can be done in a message if you want. We typically use Google Fonts and Pixvane Fonts.
CONTENT:
We're always open to different content and ideas. We often submit designs with stock images so the client can see our vision. We typically take pictures after the website launch to use their images with our vision. Lorem Ipsum is fine for paragraphs, but we ask that you write the headers in correct English. We want to be able to show the vision and identify the sections of the website.
INSPIRATION:
We typically add a couple of links in the brief of websites we like to help you get started in your design.
REVISIONS:
We do not often ask for revisions of the designs unless we see something in the design that may not appeal to the client. If there are slight changes that we want to make, we do that in the development process.
FEEDBACK:
We rarely give feedback on designs during the design process. We are working on many website projects and do not have the time to provide feedback. We usually respond if your request is well thought out and asks specific questions, but a note asking “feedback, please” usually goes unanswered.

```html
<!DOCTYPE html>
<html lang="en">
<head>
<meta charset="utf-8">
<title>Velqo – IV Nutritional Clinic</title>
<link rel="stylesheet" href="https://fonts.googleapis.com/css2?family=Outfit:wght@400;500;600;700;800&family=Arimo:ital,wght@0,400;0,700;1,400&display=swap">
<style>
:root{
  --navy:#1b1f73;
  --navy-deep:#151865;
  --green:#77a03d;
  --green-dark:#5f8a2a;
  --ink:#1c1c1c;
  --text:#4a4a4a;
  --star:#f5a623;
  --light:#e6effa;
  --white:#ffffff;
}
*{box-sizing:border-box;margin:0;padding:0}
html,body{width:1200px;height:5245px;overflow:hidden}
body{font-family:"Arimo",Arial,sans-serif;color:var(--text);background:var(--white);position:relative}
.abs{position:absolute}
h1,h2,h3,h4{font-family:"Outfit",Arial,sans-serif}
.btn{display:inline-flex;align-items:center;justify-content:center;gap:6px;border-radius:24px;font:700 13px "Arimo",Arial,sans-serif;text-transform:uppercase;letter-spacing:.2px}
.btn-navy{background:var(--navy);color:var(--white)}
.btn-white{background:var(--white);color:var(--ink)}

/* top bar */
.topbar{top:0;left:0;width:1200px;height:42px;background:var(--navy);color:#fff;font-size:13px}
.topbar span{position:absolute;top:13px}
/* nav */
.nav{top:42px;left:0;width:1200px;height:66px;background:#fff}
.brand{position:absolute;left:108px;top:14px;font:800 34px "Outfit",sans-serif;color:var(--navy);letter-spacing:1px}
.menu{position:absolute;top:24px;right:112px;display:flex;gap:30px;font-size:14.5px;color:#222}
.menu .active{color:var(--navy);border-bottom:2px solid var(--navy);padding-bottom:3px}

/* hero */
.hero{top:108px;left:0;width:1200px;height:585px;background:linear-gradient(90deg,#f1eff0 0%,#ece8ea 45%,#d9d3d2 100%)}
.hero-photo{position:absolute;right:0;top:0;width:640px;height:585px;background:linear-gradient(135deg,#e8e4e4 0%,#cfc8c6 55%,#b9b1ae 100%)}
.hero h1{position:absolute;left:105px;top:150px;font-size:104px;font-weight:800;color:var(--navy);letter-spacing:1px;line-height:1}
.hero .tag{position:absolute;left:107px;top:262px;font:700 21px "Outfit",sans-serif;color:var(--green)}
.hero .btn{position:absolute;left:105px;top:312px;width:157px;height:44px}
.dots{display:flex;gap:10px}
.dots i{width:15px;height:15px;border-radius:50%;background:#c9c9c9;display:block}
.dots i.on{background:var(--green)}

/* about */
.about{top:693px;left:0;width:1200px;height:500px;background:var(--green);color:#fff;text-align:center}
.about h2{position:absolute;top:70px;width:100%;font-size:44px;font-weight:600}
.about p{position:absolute;left:210px;top:128px;width:780px;font-size:14.5px;line-height:25.5px}
.about .btn{position:absolute;left:513px;top:298px;width:174px;height:44px}

/* offer */
.offer-title{top:1252px;width:1200px;text-align:center;font-size:42px;font-weight:500;color:var(--ink)}
.row-img{width:415px;height:382px;border-radius:14px}
.row-text{width:466px}
.row-head{display:flex;align-items:center;gap:14px}
.ico{width:66px;height:66px;border-radius:50%;background:var(--green);display:flex;align-items:center;justify-content:center}
.row-head h3{font-size:26px;font-weight:500;color:var(--ink)}
.row-text p{margin-top:16px;font-size:14.5px;line-height:25.8px;text-align:justify}
.row-text .btn{margin-top:16px;width:174px;height:44px}

/* testimonials */
.clients{top:3170px;left:0;width:1200px;height:678px;background:var(--green)}
.clients h2{position:absolute;top:120px;width:100%;text-align:center;color:#fff;font-size:42px;font-weight:500}
.card{position:absolute;top:250px;width:306px;height:262px;background:#fff;border-radius:6px;border-top:7px solid var(--navy);text-align:center;box-shadow:0 6px 16px rgba(0,0,0,.12)}
.avatar{position:absolute;left:108px;top:-46px;width:90px;height:90px;border-radius:50%;background:linear-gradient(#c9d6e6,#8da3bd);border:4px solid #fff}
.stars{margin-top:62px;color:var(--star);font-size:19px;letter-spacing:5px}
.card q{display:block;margin:14px 24px 0;font-style:italic;font-size:13.5px;line-height:25px;color:#444}
.card .who{margin-top:16px;font:600 20px "Outfit",sans-serif;color:#333}

/* contact */
.contact{top:3848px;left:0;width:1200px;height:572px;background:linear-gradient(100deg,#f3f7fd 0%,#e9f1fb 55%,#d6e6fa 100%)}
.contact h2{position:absolute;left:110px;top:95px;font-size:40px;font-weight:500;color:var(--ink)}
.field{position:absolute;width:310px;height:60px;background:#fff;border:1px solid #cdd6e0;border-radius:6px;font-size:13px;color:#333;padding:22px 22px}
.submit{position:absolute;left:435px;top:402px;width:310px;height:60px;background:var(--green);color:#fff;border-radius:6px;font:700 14px "Arimo",sans-serif;display:flex;align-items:center;justify-content:center;gap:6px}
.call{position:absolute;left:790px;top:180px}
.call h3{font-size:32px;font-weight:500;color:var(--ink);line-height:42px}
.call .num{margin-top:18px;font:600 42px "Outfit",sans-serif;color:var(--navy)}
.call p{margin-top:10px;width:310px;font-size:15px;line-height:25px;color:#555}

/* signup */
.signup{top:4420px;left:0;width:1200px;height:380px;text-align:center}
.signup h2{position:absolute;top:82px;width:100%;font-size:43px;font-weight:500;color:var(--ink);line-height:52px}
.signup p{position:absolute;left:175px;top:202px;width:850px;font-size:15px;line-height:26px;color:#444}
.signup .btn{position:absolute;left:512px;top:290px;width:176px;height:44px}

/* footer */
.footer{top:4800px;left:0;width:1200px;height:365px;background:var(--navy);color:#fff}
.footer .fname{position:absolute;left:110px;top:82px;font:700 84px "Outfit",sans-serif;letter-spacing:4px}
.footer h4{font-size:24px;font-weight:600}
.footer h4::after{content:"";display:block;width:40px;height:3px;background:var(--green);margin-top:12px}
.links{position:absolute;left:527px;top:80px}
.links ul{list-style:none;margin-top:14px;font-size:16px;line-height:26px}
.contacts{position:absolute;left:793px;top:80px}
.citem{display:flex;gap:14px;margin-top:20px;font-size:16px;line-height:22px}
.cico{width:40px;height:40px;border-radius:50%;background:var(--green);flex:none;display:flex;align-items:center;justify-content:center}
.bottom{top:5165px;left:0;width:1200px;height:80px;background:#23289a;color:#fff;font-size:13px}
.social{position:absolute;left:196px;top:33px;display:flex;gap:23px}
.social i{display:block;width:14px;height:14px;border-radius:50%;background:#fff}
.copy{position:absolute;top:33px;width:100%;text-align:center}
</style>
</head>
<body>

<div class="abs topbar">
  <span style="left:110px">&#9993;&nbsp; Mail Us : hello@velqoclinic.com</span>
  <span style="right:110px">&#9742;&nbsp; Call Us : +1 888 888 8888</span>
</div>

<header class="abs nav">
  <div class="brand">VELQO</div>
  <nav class="menu">
    <span class="active">Home</span><span>About Us</span><span>Our Services</span><span>Blog</span><span>Testimonials</span><span>Faq</span><span>Contact</span>
  </nav>
</header>

<section class="abs hero">
  <div class="hero-photo" role="img" aria-label="Smiling woman relaxing in a treatment chair holding a glass of infused water"></div>
  <h1>VELQO</h1>
  <div class="tag">WE ARE AN IV NUTRITIONAL CLINIC</div>
  <span class="btn btn-navy">Get Started</span>
  <div class="dots abs" style="left:107px;top:496px"><i></i><i class="on"></i><i></i></div>
</section>

<section class="abs about">
  <h2>ABOUT US</h2>
  <p>Lorem ipsum dolor sit amet, consectetur adipiscing elit, sed do eiusmod tempor incididunt ut labore et dolore magna aliqua. Ut enim ad minim veniam, quis nostrud exercitation ullamco laboris nisi ut aliquip ex ea commodo consequat. Duis aute irure dolor in reprehenderit in voluptate velit esse cillum dolore eu fugiat nulla pariatur. Excepteur sint occaecat cupidatat non proident, sunt in culpa qui officia deserunt mollit anim id est laborum. Lorem ipsum dolor sit amet, consectetur adipiscing elit, sed do eiusmod tempor incididunt ut labore et dolore magna aliqua. Ut enim ad minim veniam</p>
  <span class="btn btn-white">Learn More &#10148;</span>
  <svg class="abs" style="left:0;bottom:0" width="1200" height="90" viewBox="0 0 1200 90" preserveAspectRatio="none"><path d="M0 60 C250 10 420 20 620 40 C820 60 1000 85 1200 78 L1200 90 L0 90Z" fill="#fff"/></svg>
</section>

<h2 class="abs offer-title">What We Offer</h2>

<!-- row 1 -->
<div class="abs row-img" style="left:138px;top:1350px;background:linear-gradient(135deg,#e9e2dc,#c9b9ae)" role="img" aria-label="Nurse holding an IV bag filled with fresh fruit slices"></div>
<div class="abs row-text" style="left:594px;top:1342px">
  <div class="row-head"><div class="ico"><svg width="30" height="30" viewBox="0 0 24 24" fill="none" stroke="#fff" stroke-width="1.6"><rect x="6" y="3" width="9" height="12" rx="2"/><path d="M10.5 15v6M15 8h4v10"/></svg></div><h3>Lorem ipsum dolor sit amet</h3></div>
  <p>Lorem ipsum dolor sit amet, consectetur adipiscing elit, sed do eiusmod tempor incididunt ut labore et dolore magna aliqua. Ut enim ad minim veniam, quis nostrud exercitation ullamco laboris nisi ut aliquip ex ea commodo consequat. Duis aute irure dolor in reprehenderit in voluptate velit esse cillum dolore eu fugiat nulla pariatur. Excepteur sint occaecat cupidatat non proident, sunt in culpa qui officia deserunt mollit anim id est laborum. Lorem ipsum dolor sit amet, consectetur adipiscing elit, sed do eiusmod tempor incididunt ut labore et dolore magna aliqua. Ut enim ad minim veniam</p>
  <span class="btn btn-navy">Learn More &#10148;</span>
</div>

<!-- row 2 -->
<div class="abs row-text" style="left:138px;top:1792px">
  <div class="row-head"><div class="ico"><svg width="30" height="30" viewBox="0 0 24 24" fill="none" stroke="#fff" stroke-width="1.6"><path d="M5 19l6-6M9 9l6 6M12 6l6 6-4 4-6-6z"/></svg></div><h3>Lorem ipsum dolor sit amet</h3></div>
  <p>Lorem ipsum dolor sit amet, consectetur adipiscing elit, sed do eiusmod tempor incididunt ut labore et dolore magna aliqua. Ut enim ad minim veniam, quis nostrud exercitation ullamco laboris nisi ut aliquip ex ea commodo consequat. Duis aute irure dolor in reprehenderit in voluptate velit esse cillum dolore eu fugiat nulla pariatur. Excepteur sint occaecat cupidatat non proident, sunt in culpa qui officia deserunt mollit anim id est laborum. Lorem ipsum dolor sit amet, consectetur adipiscing elit, sed do eiusmod tempor incididunt ut labore et dolore magna aliqua. Ut enim ad minim veniam</p>
  <span class="btn btn-navy">Learn More &#10148;</span>
</div>
<div class="abs row-img" style="left:645px;top:1799px;background:linear-gradient(135deg,#ece9e6,#cfc7c0)" role="img" aria-label="Nurse preparing an IV drip for a seated patient"></div>

<!-- row 3 -->
<div class="abs row-img" style="left:138px;top:2248px;background:linear-gradient(135deg,#eef0f2,#cdd3d8)" role="img" aria-label="Patient in white robe receiving an IV infusion"></div>
<div class="abs row-text" style="left:594px;top:2241px">
  <div class="row-head"><div class="ico"><svg width="30" height="30" viewBox="0 0 24 24" fill="none" stroke="#fff" stroke-width="1.6"><path d="M4 20V9h16v11M4 13h16M8 4v5M16 4v5"/></svg></div><h3>Lorem ipsum dolor sit amet</h3></div>
  <p>Lorem ipsum dolor sit amet, consectetur adipiscing elit, sed do eiusmod tempor incididunt ut labore et dolore magna aliqua. Ut enim ad minim veniam, quis nostrud exercitation ullamco laboris nisi ut aliquip ex ea commodo consequat. Duis aute irure dolor in reprehenderit in voluptate velit esse cillum dolore eu fugiat nulla pariatur. Excepteur sint occaecat cupidatat non proident, sunt in culpa qui officia deserunt mollit anim id est laborum. Lorem ipsum dolor sit amet, consectetur adipiscing elit, sed do eiusmod tempor incididunt ut labore et dolore magna aliqua. Ut enim ad minim veniam</p>
  <span class="btn btn-navy">Learn More &#10148;</span>
</div>

<!-- row 4 -->
<div class="abs row-text" style="left:138px;top:2690px">
  <div class="row-head"><div class="ico"><svg width="30" height="30" viewBox="0 0 24 24" fill="none" stroke="#fff" stroke-width="1.6"><rect x="7" y="3" width="10" height="16" rx="2"/><path d="M12 19v3M10 9h4M12 7v4"/></svg></div><h3>Lorem ipsum dolor sit amet</h3></div>
  <p>Lorem ipsum dolor sit amet, consectetur adipiscing elit, sed do eiusmod tempor incididunt ut labore et dolore magna aliqua. Ut enim ad minim veniam, quis nostrud exercitation ullamco laboris nisi ut aliquip ex ea commodo consequat. Duis aute irure dolor in reprehenderit in voluptate velit esse cillum dolore eu fugiat nulla pariatur. Excepteur sint occaecat cupidatat non proident, sunt in culpa qui officia deserunt mollit anim id est laborum. Lorem ipsum dolor sit amet, consectetur adipiscing elit, sed do eiusmod tempor incididunt ut labore et dolore magna aliqua. Ut enim ad minim veniam</p>
  <span class="btn btn-navy">Learn More &#10148;</span>
</div>
<div class="abs row-img" style="left:645px;top:2697px;background:linear-gradient(135deg,#e4ebee,#b9c7cf)" role="img" aria-label="Woman resting in a clinic recliner during IV therapy"></div>

<section class="abs clients">
  <svg class="abs" style="left:0;top:0" width="1200" height="60" viewBox="0 0 1200 60" preserveAspectRatio="none"><path d="M0 0 H1200 V30 C1000 5 820 5 620 25 C420 45 200 55 0 10Z" fill="#fff"/></svg>
  <h2>Clients Share Their Experience</h2>
  <div class="card" style="left:112px"><div class="avatar" role="img" aria-label="Client portrait"></div><div class="stars">★★★★★</div><q>Lorem ipsum dolor sit amet, consectetur adipiscing elit, sed do eiusmod tempor incididunt ut labore et dolore magna aliqua.</q><div class="who">- Maria L.</div></div>
  <div class="card" style="left:447px"><div class="avatar" role="img" aria-label="Client portrait"></div><div class="stars">★★★★★</div><q>Lorem ipsum dolor sit amet, consectetur adipiscing elit, sed do eiusmod tempor incididunt ut labore et dolore magna aliqua.</q><div class="who">- Daniel R.</div></div>
  <div class="card" style="left:782px"><div class="avatar" role="img" aria-label="Client portrait"></div><div class="stars">★★★★★</div><q>Lorem ipsum dolor sit amet, consectetur adipiscing elit, sed do eiusmod tempor incididunt ut labore et dolore magna aliqua.</q><div class="who">- Priya S.</div></div>
  <div class="abs" style="left:688px;top:498px;font:700 56px 'Outfit',sans-serif;color:var(--navy);line-height:1">&#8221;</div>
  <div class="dots abs" style="left:565px;top:570px"><i style="background:#d8d8d8"></i><i style="background:#b7cf8e"></i><i style="background:#d8d8d8"></i></div>
</section>

<section class="abs contact">
  <h2>Get In Touch</h2>
  <div class="field" style="left:108px;top:170px">First name</div>
  <div class="field" style="left:108px;top:247px">Last name</div>
  <div class="field" style="left:108px;top:324px">Email</div>
  <div class="field" style="left:108px;top:402px">Phone</div>
  <div class="field" style="left:435px;top:170px;height:215px">Message</div>
  <div class="submit">SUBMIT <svg width="14" height="14" viewBox="0 0 24 24" fill="#fff"><path d="M2 11l20-9-7 20-3-8z"/></svg></div>
  <div class="call">
    <h3>Need our service?<br>Please call us:</h3>
    <div class="num">+1 888 888 8888</div>
    <p>We would love to see how we can help you solve your neck and back problems in the best pain free methods</p>
  </div>
</section>

<section class="abs signup">
  <h2>Sign up for email and texts today, and enjoy<br>15% off your next IV or injection therapy!</h2>
  <p>Lorem ipsum dolor sit amet, consectetur adipiscing elit, sed do eiusmod tempor incididunt ut labore et dolore magna aliqua. Ut enim ad minim veniam, quis nostrud exercitation ullamco laboris nisi ut aliquip ex ea commodo consequat.</p>
  <span class="btn btn-navy">Sign Up Now</span>
</section>

<footer class="abs footer">
  <div class="fname">VELQO</div>
  <div class="links"><h4>Quick Links</h4>
    <ul><li>Home</li><li>About Us</li><li>Our Services</li><li>Reviews</li><li>Blog</li><li>FAQ</li><li>Contact Us</li></ul>
  </div>
  <div class="contacts"><h4>Contact Us</h4>
    <div class="citem"><div class="cico"><svg width="16" height="16" viewBox="0 0 24 24" fill="#fff"><path d="M12 2a7 7 0 0 0-7 7c0 5 7 13 7 13s7-8 7-13a7 7 0 0 0-7-7zm0 9.5A2.5 2.5 0 1 1 12 6.5a2.5 2.5 0 0 1 0 5z"/></svg></div><div>123,Lorem ipsum dolor sit<br>amet, consectetur</div></div>
    <div class="citem"><div class="cico"><svg width="16" height="16" viewBox="0 0 24 24" fill="#fff"><path d="M6.6 10.8a15 15 0 0 0 6.6 6.6l2.2-2.2a1 1 0 0 1 1-.25 11.4 11.4 0 0 0 3.6.57 1 1 0 0 1 1 1V20a1 1 0 0 1-1 1A17 17 0 0 1 3 4a1 1 0 0 1 1-1h3.5a1 1 0 0 1 1 1c0 1.25.2 2.45.57 3.57a1 1 0 0 1-.25 1z"/></svg></div><div>Phone :<br>+1 888 888 8888</div></div>
    <div class="citem"><div class="cico"><svg width="16" height="16" viewBox="0 0 24 24" fill="#fff"><path d="M3 5h18v14H3z M3 6l9 7 9-7" stroke="#77a03d" stroke-width="1.5"/></svg></div><div>Email :<br>hello@velqoclinic.com</div></div>
  </div>
</footer>

<div class="abs bottom">
  <div class="social"><i></i><i style="background:var(--green)"></i><i></i></div>
  <div class="copy">&copy; Copyrights 2024 | All Rights Reserved</div>
</div>

</body>
</html>
```